Fresh, modern, fun business card for pediatric dental practice

Need a business card for fresh, modern, fun pediatric dental practice

Clean look that matches our website's font and colors

We prefer the look of curved corners on business cards

Target Market(s)

parents (mothers) of young children, professionals, mid-high class

Industry/Entity Type

Dental

Contact Information for Business Card

Maplebrook Pediatric Dentistry
482 Quarry Lane
Suite 517
Elmvale, PA 17590
717.555.0193
www.maplebrookkidsdental.example

Mei-Ran Tsai, DMD
Corinne Walbeck, DMD
(we are working on our email address, but we would like that on the card as well)

Font styles to use
Sans Serif

Requirements
Must have
• All info; we would also like to make cards for individual staff members
• colors from our website and color palatte, attatched
• use same font and design as website for branding
Nice to have
• clean, simple card that has a pop of color
• we would like to see a few designs with our tag line "where smiles get brighter"
• we are not sure if we want to have it on there or not
• we would like to see a few designs incorporating the ribbon graphic on our website where the word WELCOME is

```html
<!DOCTYPE html>
<html lang="en">
<head>
<meta charset="utf-8">
<title>Maplebrook Pediatric Dentistry – Business Card</title>
<link href="https://fonts.googleapis.com/css2?family=Work+Sans:wght@400;500;600;700&display=swap" rel="stylesheet">
<style>
  :root{
    --stage:#e9e6e2;
    --card:#1c1c1d;
    --edge:#c9a314;
    --sun:#fdb927;
    --berry:#d126a6;
    --silver:#8d8f93;
    --ink:#f3f3f3;
    --rule:#e6e6e6;
  }
  *{margin:0;padding:0;box-sizing:border-box}
  html,body{width:1200px;height:715px;overflow:hidden}
  body{background:var(--stage);font-family:"Work Sans",Arial,sans-serif;position:relative}
  .card{position:absolute;top:203px;width:540px;height:309px;background:var(--card);border-radius:14px;overflow:hidden;box-shadow:0 6px 18px rgba(0,0,0,.18)}
  .card--front{left:40px;box-shadow:0 6px 18px rgba(0,0,0,.18),0 0 0 3px var(--edge)}
  .card--back{left:620px}

  .front-mark{position:absolute;left:0;right:0;top:112px;text-align:center;color:var(--silver);font-weight:600;font-size:27px;letter-spacing:.5px;display:flex;align-items:center;justify-content:center;gap:12px}
  .front-mark .dot{width:22px;height:22px;border-radius:50%;background:var(--silver)}

  .person{position:absolute;left:46px;top:88px}
  .person__name{color:var(--sun);font-weight:700;font-size:19px;letter-spacing:.3px;text-transform:uppercase}
  .person__title{color:var(--ink);font-size:10px;margin-top:2px}
  .rule{position:absolute;left:46px;right:40px;top:132px;height:1px;background:var(--rule)}
  .contact{position:absolute;left:46px;top:146px;list-style:none;color:var(--ink);font-size:12px;line-height:19px}
  .contact li{display:flex;align-items:center;gap:8px}
  .contact svg{width:9px;height:9px;fill:var(--sun)}

  .brand{position:absolute;right:40px;top:82px;text-align:right;color:var(--sun);font-weight:600;line-height:1}
  .brand__name{font-size:30px}
  .brand__sub{font-size:15px;margin-top:3px;letter-spacing:.6px}

  .address{position:absolute;right:40px;top:206px;text-align:right;color:var(--ink);font-size:12px;line-height:17px}

  .band{position:absolute;left:0;right:0;bottom:22px;height:16px}
  .band__bar{position:absolute;left:40px;right:46px;top:0;bottom:0;background:var(--sun)}
  .band__cap{position:absolute;width:20px;background:var(--berry)}
  .band__cap--start{left:14px;top:-14px;height:14px}
  .band__cap--end{right:20px;top:0;height:16px}
</style>
</head>
<body>
  <section class="card card--front" aria-label="Card front">
    <div class="front-mark"><span class="dot"></span>Maplebrook Pediatric Dentistry</div>
  </section>

  <section class="card card--back" aria-label="Card back">
    <div class="person">
      <div class="person__name">Corinne Walbeck</div>
      <div class="person__title">DMD</div>
    </div>
    <div class="rule"></div>
    <ul class="contact">
      <li><svg viewBox="0 0 10 10"><path d="M2 0h2l1 2.5-1.3 1a6 6 0 0 0 2.8 2.8l1-1.3L10 6v2a2 2 0 0 1-2 2A8 8 0 0 1 0 2a2 2 0 0 1 2-2z"/></svg>717.555.0193</li>
      <li><svg viewBox="0 0 10 10"><path d="M0 2h10v6H0zM1 3l4 2.6L9 3v-.2H1z"/></svg>hello@maplebrookkids.example</li>
      <li><svg viewBox="0 0 10 10"><circle cx="5" cy="5" r="5"/></svg>www.maplebrookkidsdental.example</li>
    </ul>
    <div class="brand">
      <div class="brand__name">Maplebrook</div>
      <div class="brand__sub">pediatric dentistry</div>
    </div>
    <div class="address">482 Quarry Lane<br>Suite 517 Elmvale, PA 17590</div>
    <div class="band">
      <span class="band__cap band__cap--start"></span>
      <span class="band__bar"></span>
      <span class="band__cap band__cap--end"></span>
    </div>
  </section>
</body>
</html>
```